We need a new business card that reflects who we are. Professional, classy, modern, and service ori

We need a business card design for a window coverings design company in Kansas City called Bright Lane Interiors. We offer professional, modern, and high quality window covering products. We are looking to portray an image of a big, national franchise. We are a 5 location (with showrooms) business with 10 professional designers and 4 professional installers. These cards will be used with Thank you cards, given to realtors, and asked for referrals with.

Target Market(s)

Kansas City

Industry/Entity Type

Business

Contact Information for Business Card

We would like our card to look clean and simple on the front, featuring our logo and Marlow Fenwick's. Our designers' phone numbers and emails should be displayed as well as their title.

Font styles to use
Sans Serif

Colors

Designer to choose colors to be used in the design.

Requirements
Must have
• Front - Logos, name, phone number, email address
• Back - Showroom locations, social media? Appt date/time?
Nice to have
• I would like a clean and modern look (not contemporary. I like a white background, but I am open to ideas. Looking for a "National chain" look for a small business.
Should not have
• Too much busyness.

```html
<!DOCTYPE html>
<html lang="en">
<head>
<meta charset="utf-8">
<title>Bright Lane Interiors – Business Card</title>
<link rel="stylesheet" href="https://fonts.googleapis.com/css2?family=Roboto:wght@400;500;700&family=Roboto+Condensed:wght@700&display=swap">
<style>
  :root {
    --backdrop: #2a2a2a;
    --card: #f4f4f4;
    --brand-red: #c7444a;
    --ink: #1c1c1c;
    --grey-text: #555555;
    --rule: #c9c9c9;
    --dots: #8a8a8a;
  }
  * { box-sizing: border-box; margin: 0; padding: 0; }
  html, body { width: 1200px; height: 960px; overflow: hidden; }
  body {
    background: var(--backdrop);
    font-family: "Roboto", Arial, sans-serif;
    position: relative;
  }
  .card {
    position: absolute;
    left: 320px;
    width: 600px;
    background: var(--card);
    overflow: hidden;
  }

  /* Front */
  .card-front { top: 100px; height: 352px; }
  .front-band {
    position: absolute; left: 0; bottom: 0; width: 100%; height: 24px;
  }
  .brand-block {
    position: absolute; left: 44px; top: 192px; width: 248px; text-align: center;
  }
  .brand-mark { display: flex; align-items: center; justify-content: center; gap: 8px; }
  .brand-square { width: 14px; height: 14px; background: var(--brand-red); flex: none; }
  .brand-name {
    font-size: 22px; font-weight: 500; color: var(--ink); letter-spacing: 0.2px; white-space: nowrap;
  }
  .brand-tagline {
    margin-top: 8px; font-size: 11.5px; color: var(--ink); white-space: nowrap;
  }
  .front-divider {
    position: absolute; left: 306px; top: 115px; width: 1px; height: 130px; background: var(--rule);
  }
  .person {
    position: absolute; left: 335px; top: 125px;
  }
  .person-name {
    font-family: "Roboto Condensed", "Arial Narrow", sans-serif;
    font-size: 24px; font-weight: 700; color: var(--brand-red); line-height: 1;
  }
  .person-title {
    margin-top: 6px; font-size: 15px; font-weight: 700; color: var(--ink); letter-spacing: 0.3px;
  }
  .contact-list { list-style: none; margin-top: 12px; }
  .contact-list li {
    display: flex; align-items: center; gap: 9px;
    font-size: 14px; color: var(--grey-text); line-height: 19px;
  }
  .contact-list svg { width: 12px; height: 12px; fill: var(--brand-red); flex: none; }

  /* Back */
  .card-back { top: 492px; height: 343px; }
  .back-brand {
    position: absolute; right: 58px; top: 66px; display: flex; align-items: center; gap: 7px;
  }
  .back-brand .brand-name { font-size: 18px; }
  .appointment-title {
    position: absolute; left: 42px; top: 88px;
    font-size: 20px; font-weight: 500; color: var(--brand-red);
  }
  .field {
    position: absolute; left: 42px; display: flex; align-items: baseline;
    font-size: 16px; color: var(--brand-red);
  }
  .field-fill { border-bottom: 1px dotted var(--dots); height: 1px; margin-left: 8px; }
  .field-name { top: 139px; }
  .field-date { top: 181px; }
  .field-ampm { font-size: 13px; margin-left: 6px; }
  .locations {
    position: absolute; left: 42px; top: 233px;
    font-size: 14.5px; font-weight: 700; color: var(--grey-text); letter-spacing: 0.2px; white-space: nowrap;
  }
  .social-row { position: absolute; left: 44px; top: 280px; display: flex; gap: 3px; }
  .social-dot { width: 21px; height: 21px; border-radius: 50%; background: var(--brand-red); }
  .partner {
    position: absolute; right: 56px; top: 281px;
    font-size: 15px; font-weight: 700; color: var(--grey-text);
  }
</style>
</head>
<body>

<section class="card card-front" aria-label="Business card front">
  <div class="brand-block">
    <div class="brand-mark">
      <span class="brand-square"></span>
      <span class="brand-name">Bright Lane Interiors</span>
    </div>
    <p class="brand-tagline">Blinds, Shades, Shutters, Draperies &amp; Decor</p>
  </div>

  <div class="front-divider"></div>

  <div class="person">
    <h1 class="person-name">JORDAN AVERY</h1>
    <p class="person-title">DESIGNER</p>
    <ul class="contact-list">
      <li>
        <svg viewBox="0 0 24 24" aria-hidden="true"><path d="M6.6 10.8a15.1 15.1 0 0 0 6.6 6.6l2.2-2.2c.3-.3.7-.4 1-.2 1.1.4 2.3.6 3.6.6.6 0 1 .4 1 1V20c0 .6-.4 1-1 1C10.6 21 3 13.4 3 4c0-.6.4-1 1-1h3.5c.6 0 1 .4 1 1 0 1.3.2 2.5.6 3.6.1.3 0 .7-.2 1z"/></svg>
        913.555.0148
      </li>
      <li>
        <svg viewBox="0 0 24 24" aria-hidden="true"><path d="M2 5h20v2l-10 6L2 7z"/><path d="M2 9l10 6 10-6v10H2z"/></svg>
        info@brightlaneinteriors.com
      </li>
      <li>
        <svg viewBox="0 0 24 24" aria-hidden="true"><circle cx="12" cy="12" r="10"/><path d="M2 12h20M12 2c3 3 3 17 0 20M12 2c-3 3-3 17 0 20" stroke="#f4f4f4" stroke-width="1.6" fill="none"/></svg>
        brightlaneinteriors.com
      </li>
    </ul>
  </div>

  <svg class="front-band" viewBox="0 0 600 24" preserveAspectRatio="none" aria-hidden="true">
    <polygon points="0,0 396,0 390,24 0,24" fill="var(--brand-red)"/>
    <polygon points="396,0 400,0 394,24 390,24" fill="#ffffff"/>
    <polygon points="400,0 600,0 600,24 394,24" fill="var(--ink)"/>
  </svg>
</section>

<section class="card card-back" aria-label="Business card back">
  <div class="back-brand">
    <span class="brand-square"></span>
    <span class="brand-name">Bright Lane Interiors</span>
  </div>

  <h2 class="appointment-title">Next Appointment</h2>

  <div class="field field-name">
    <span>Name :</span><span class="field-fill" style="width:438px"></span>
  </div>
  <div class="field field-date">
    <span>Date :</span><span class="field-fill" style="width:214px"></span>
    <span style="margin-left:2px">Time :</span><span class="field-fill" style="width:132px"></span>
    <span class="field-ampm">AM/PM</span>
  </div>

  <p class="locations">WESTFIELD | BRIAR HILL | OAK CROSSING | NORTHGATE | RIVERSIDE</p>

  <div class="social-row" aria-label="Social media">
    <span class="social-dot"></span>
    <span class="social-dot"></span>
    <span class="social-dot"></span>
    <span class="social-dot"></span>
  </div>

  <p class="partner">Marlow Fenwick</p>
</section>

</body>
</html>
```